MS word document templates for consultancy

I need the following templates for my business using my logo as branding.

- General report template
- Letter head template
- Tender proposal template

The templates should be sleek and with minimal colors, but with a small amount of green and grey where appropriate (as per attached logo and email signature). Font should be consistent with the text in the email signature.

```html
<!DOCTYPE html>
<html lang="en">
<head>
<meta charset="utf-8">
<title>Ashby Consulting – Letterhead and Report Templates</title>
<link rel="stylesheet" href="https://fonts.googleapis.com/css2?family=Arimo:wght@400&family=Roboto:wght@400;500;700&family=Roboto+Condensed:wght@500;600&display=swap">
<style>
  :root {
    --backdrop: #9c9c9c;
    --paper: #ffffff;
    --brand-green: #2a9642;
    --ink: #111111;
    --body-grey: #4f4f4f;
    --rule-grey: #a9a9a9;
  }
  * { box-sizing: border-box; margin: 0; padding: 0; }
  html, body { width: 1200px; height: 982px; overflow: hidden; }
  body { background: var(--backdrop); position: relative; font-family: "Arimo", Arial, sans-serif; }

  .page {
    position: absolute; top: 130px; width: 511px; height: 722px;
    background: var(--paper);
    box-shadow: 3px 3px 6px rgba(0,0,0,0.35);
  }
  .page--letter { left: 72px; }
  .page--report { left: 617px; }

  /* Header */
  .brand-name {
    position: absolute; left: 42px; top: 36px;
    font-family: "Roboto", sans-serif; font-weight: 400;
    font-size: 22px; color: var(--ink); line-height: 1;
  }
  .contact { position: absolute; left: 337px; top: 34px; font-family: "Roboto", sans-serif; font-size: 8.4px; line-height: 10.5px; }
  .contact__name { color: var(--brand-green); font-weight: 700; }
  .contact__role { color: var(--body-grey); }
  .contact__divider { position: absolute; left: 415px; top: 35px; width: 1px; height: 17px; background: var(--ink); }
  .contact__phone { position: absolute; left: 422px; top: 44px; font-family: "Roboto", sans-serif; font-size: 8.4px; color: var(--body-grey); display: flex; align-items: center; gap: 2px; }
  .rule-green { position: absolute; left: 0; right: 0; top: 60px; height: 3px; background: var(--brand-green); }
  .rule-black { position: absolute; left: 0; right: 0; top: 68px; height: 1.5px; background: var(--ink); }

  /* Letter */
  .letter { position: absolute; left: 46px; top: 222px; width: 422px; color: var(--body-grey); }
  .letter__salutation { font-size: 11.4px; margin-bottom: 19px; }
  .letter p, .section p { font-size: 9px; line-height: 10.5px; margin-bottom: 9px; }
  .letter__closing { font-size: 6.4px; margin-top: 22px; }
  .signature { display: block; width: 62px; height: 18px; margin-top: 14px; background: linear-gradient(90deg, #d8d8d8, #efefef); }

  /* Report */
  .report-banner {
    position: absolute; left: 46px; top: 109px; width: 415px; height: 40px;
    background: var(--brand-green); color: #fff;
    font-family: "Roboto Condensed", sans-serif; font-weight: 500;
    font-size: 34px; line-height: 40px; text-align: center; letter-spacing: 0.5px;
  }
  .section { position: absolute; left: 46px; width: 422px; color: var(--body-grey); }
  .section h2 {
    font-family: "Roboto Condensed", sans-serif; font-weight: 600;
    font-size: 17.5px; color: var(--brand-green); line-height: 18px;
    width: 415px; border-bottom: 1px solid var(--rule-grey); padding-bottom: 1px; margin-bottom: 7px;
  }
</style>
</head>
<body>

<article class="page page--letter">
  <header>
    <div class="brand-name">Ashby Consulting</div>
    <div class="contact"><div class="contact__name">Tom Reilly</div><div class="contact__role">Managing Director</div></div>
    <div class="contact__divider"></div>
    <div class="contact__phone">
      <svg width="7" height="6" viewBox="0 0 14 12"><path d="M1 4c0-2 3-3 6-3s6 1 6 3v1h-3V3.5H4V5H1z M3 6h8l2 5H1z" fill="#2a9642"/></svg>
      0400 555 019
    </div>
    <div class="rule-green"></div>
    <div class="rule-black"></div>
  </header>

  <section class="letter">
    <div class="letter__salutation">Dear Mr. Hale,</div>
    <p>Lorem ipsum dolor sit amet, consectetuer adipiscing elit, sed diam nonmmy nibh euismod tincidunt ut laor eet dolore magna aliquam erat volutpat. Ut wisi enim ad minim veniam, quis nostrud exerci tationmcorper suscipit lobortis nisl ut aliquip ex ea commodo consequat. Duis autem vel eum iriure dolor in hendrerit in vulputate velit esse molestie consequat, vel illum dolore eu feugiat</p>
    <p>Rorem ipsum dolor sit amet, consectetuer adipiscing elit, sed diam nonmmy nibh euismod tincidunt ut laor eet dolore magna aliquam erat volutpat. Ut wisi enim ad minim veniam, quis nostrud exerci tationmcorper suscipit lobortis nisl ut aliquip ex ea commodo consequat. Duis autem vel eum iriure dolor in hendrerit in vulputate velit esse molest</p>
    <p>Dorem ipsum dolor sit amet, consectetuer adipiscing elit, sed diam nonmmy nibh euismod tincidunt ut laor eet dolore magna aliquam erat volutpat. Ut wisi enim ad minim veniam, quis nostrud exerci tationmcorper suscipit lobortis nisl ut aliquip ex ea commodo consequat. Duis autem vel eum iriure dolor in hendrerit in suscipit lobortis nisl ut aliquip ex ea commodo consequat. Duis autem vel eum iriure dolor in hendrerit in vulputate velit esse molestie consequat, vel illum</p>
    <p>Sorem ipsum dolor sit amet, consectetuer adipiscing elit, sed diam nonmmy nibh euismod tincidunt ut laor eet dolore magna aliquam erat volutpat. Ut wisi enim ad minim veniam, quis nostrud exerci tationmcorper suscipit lobortis nisl ut aliquip ex ea commodo consequat. Duis autem vel eum iriure dolor in</p>
    <div class="letter__closing">Sincerely,</div>
    <span class="signature" role="img" aria-label="Handwritten signature of the sender"></span>
  </section>
</article>

<article class="page page--report">
  <header>
    <div class="brand-name">Ashby Consulting</div>
    <div class="contact"><div class="contact__name">Tom Reilly</div><div class="contact__role">Managing Director</div></div>
    <div class="contact__divider"></div>
    <div class="contact__phone">
      <svg width="7" height="6" viewBox="0 0 14 12"><path d="M1 4c0-2 3-3 6-3s6 1 6 3v1h-3V3.5H4V5H1z M3 6h8l2 5H1z" fill="#2a9642"/></svg>
      0400 555 019
    </div>
    <div class="rule-green"></div>
    <div class="rule-black"></div>
  </header>

  <h1 class="report-banner">ANNUAL REPORT 2025</h1>

  <section class="section" style="top:167px">
    <h2>Title:</h2>
    <p>Lorem ipsum dolor sit amet, consectetuer adipiscing elit, sed diam nonmmy nibh euismod tincidunt ut laor eet dolore magna aliquam erat volutpat. Ut wisi enim ad minim veniam, quis nostrud exerci tationmcorper suscipit lobortis nisl ut aliquip ex ea commodo consequat. Duis autem vel eum iriure dolor in hendrerit in vulputate velit esse molestie consequat, vel illum dolore eu feugiat</p>
  </section>

  <section class="section" style="top:249px">
    <h2>Table of contents:</h2>
    <p>Lorem ipsum dolor sit amet, consectetuer adipiscing elit, sed diam nonmmy nibh euismod tincidunt ut laor eet dolore magna aliquam erat volutpat. Ut wisi enim ad minim veniam, quis nostrud exerci tationmcorper suscipit lobortis nisl ut aliquip ex ea commodo consequat. Duis autem vel eum iriure dolor in hendrerit in vulputate velit esse molestie consequat, vel illum dolore eu feugiat</p>
    <p>Rorem ipsum dolor sit amet, consectetuer adipiscing elit, sed diam nonmmy nibh euismod tincidunt ut laor eet dolore magna aliquam erat volutpat. Ut wisi enim ad minim veniam, quis nostrud exerci tationmcorper suscipit lobortis nisl ut aliquip ex ea commodo consequat. Duis autem vel eum iriure dolor in hendrerit in vulputate velit esse molest</p>
  </section>

  <section class="section" style="top:381px">
    <h2>Executive Summary:</h2>
    <p>Lorem ipsum dolor sit amet, consectetuer adipiscing elit, sed diam nonmmy nibh euismod tincidunt ut laor eet dolore magna aliquam erat volutpat. Ut wisi enim ad minim veniam, quis nostrud exerci tationmcorper suscipit lobortis nisl ut aliquip ex ea commodo consequat. Duis autem vel eum iriure dolor in hendrerit in vulputate velit esse molestie consequat, vel illum dolore eu feugiat</p>
  </section>

  <section class="section" style="top:465px">
    <h2>Quick Summary (Introduction):</h2>
    <p>Lorem ipsum dolor sit amet, consectetuer adipiscing elit, sed diam nonmmy nibh euismod tincidunt ut laor eet dolore magna aliquam erat volutpat. Ut wisi enim ad minim veniam, quis nostrud exerci tationmcorper suscipit lobortis nisl ut aliquip ex ea commodo consequat. Duis autem vel eum iriure dolor in hendrerit in vulputate velit esse molestie consequat, vel illum dolore eu feugiat</p>
    <p>Rorem ipsum dolor sit amet, consectetuer adipiscing elit, sed diam nonmmy nibh euismod tincidunt ut laor eet dolore magna aliquam erat volutpat. Ut wisi enim ad minim veniam, quis nostrud exerci tationmcorper suscipit lobortis nisl ut aliquip ex ea commodo consequat. Duis autem vel eum iriure dolor in hendrerit in vulputate velit esse molest</p>
  </section>

  <section class="section" style="top:593px">
    <h2>Conclusion:</h2>
    <p>Lorem ipsum dolor sit amet, consectetuer adipiscing elit, sed diam nonmmy nibh euismod tincidunt ut laor eet dolore magna aliquam erat volutpat. Ut wisi enim ad minim veniam, quis nostrud exerci tationmcorper suscipit lobortis nisl ut aliquip ex ea commodo consequat. Duis autem vel eum iriure dolor in hendrerit in vulputate velit esse molestie consequat, vel illum dolore eu feugiat</p>
  </section>
</article>

</body>
</html>
```